Brightfield Homes needs a web design and brand identifier

Brightfield Homes is a pioneering approach by Victorian councils and four greenhouse alliances to support low income households to install solar systems with no upfront costs.

Brightfield Homes will commence in May 2017.

Brightfield Homes is looking for a designer to create a website banner incorporating a brand identifier for Brightfield Homes. The brand identifier will be used in Brightfield Homes promotional materials, such as flyers and mail outs.

The website banner and brand identifier should engender trust and confidence in the target group (retirees).

Reason: Hi, Thank you for your work so far. We've been given advice to get a separate logo designed (instead of trying to include this as part of the banner design). Sorry for not realising this until now - we're new to all this. So, I have a couple of preliminary logo designs that are being considered by our project control group. I will forward a copy of the logo once we have it. The project control group is looking for a web design that is unique to Brightfield Homes and a design that draws on the key elements of the program (i.e. it helps people save money and take control). The site should be friendly but not too informal as the target group is seniors. Here's a link to another community energy organisation: www.kindlewattnet.com.au/ Apologies again for the delays. Cheers, Doug

Target Market(s)

Home owning, low income, retirees

Industry/Entity Type

Non Profit

Number of Pages Required

1 page

Font styles to use
Sans Serif

Requirements
Must have
• Use of Brightfield Home name
• Must promote Brightfield Homes as safe, reliable and trustworthy
Nice to have
• Blue - to engender sense of safety and confidence (open to suggestions, though)
• Solar panels / the sun
Should not have
• Anything that is hard to read
• anything that promotes riskyness

```html
<!DOCTYPE html>
<html lang="en">
<head>
<meta charset="utf-8">
<title>Brightfield Homes</title>
<link rel="stylesheet" href="https://fonts.googleapis.com/css2?family=Raleway:wght@500;600;700;800&family=Open+Sans:wght@400;600;700&display=swap">
<style>
:root{
  --navy:#0b2c5e;
  --navy-deep:#082450;
  --cyan:#1aabd3;
  --cyan-text:#1ba3cf;
  --ink:#1b2a44;
  --grey:#5b6574;
  --line:#cfe0ea;
  --pale:#e9eff3;
  --white:#ffffff;
}
*{box-sizing:border-box;margin:0;padding:0}
html,body{width:1200px;height:3077px;overflow:hidden}
body{position:relative;background:var(--white);font-family:"Open Sans",Arial,sans-serif;color:var(--ink)}
.abs{position:absolute}

/* header */
.site-header{left:0;top:0;width:1200px;height:78px;background:var(--white)}
.brand{left:172px;top:20px;font-family:"Raleway",sans-serif;font-weight:800;font-size:31px;color:var(--navy);letter-spacing:.5px}
.call{left:680px;top:18px;display:flex;align-items:center;gap:10px}
.call-text small{display:block;font-size:11px;font-weight:700;color:var(--navy);letter-spacing:.3px}
.call-text strong{display:block;font-size:23px;font-weight:600;color:var(--navy);line-height:1}
.quote-btn{left:888px;top:26px;width:140px;height:30px;border-radius:15px;background:var(--cyan);color:var(--white);font-size:12px;font-weight:700;display:flex;align-items:center;justify-content:center}

/* hero */
.hero-band{left:0;top:78px;width:1200px;height:580px}
.main-nav{left:0;top:90px;width:1200px;display:flex;justify-content:center;gap:38px;font-size:13px;font-weight:700;color:var(--white);letter-spacing:.2px}
.hero-photo{left:172px;top:127px;width:856px;height:468px;border-radius:6px;background:linear-gradient(120deg,#5b8c3f 0%,#a9b86a 35%,#d8b98a 60%,#7aa1c4 100%)}
.hero-shade{left:172px;top:127px;width:856px;height:468px;border-radius:6px;background:linear-gradient(90deg,rgba(10,30,60,.55),rgba(10,30,60,0) 60%)}
.hero-kicker{left:193px;top:160px;font-family:"Raleway",sans-serif;font-size:24px;font-weight:600;color:var(--white)}
.hero-title{left:191px;top:182px;font-family:"Raleway",sans-serif;font-size:66px;font-weight:800;color:var(--white);line-height:1}
.hero-copy{left:193px;top:256px;width:420px;font-size:17px;font-weight:600;color:var(--white);line-height:1.3}

/* welcome */
.section-title{font-family:"Raleway",sans-serif;font-weight:700;color:var(--navy);text-align:center}
.rule{height:3px;width:48px;background:var(--cyan)}
.welcome-title{left:0;top:705px;width:1200px;font-size:33px}
.welcome-rule{left:576px;top:755px}
.video-thumb{left:172px;top:796px;width:427px;height:240px;background:linear-gradient(180deg,#8fb8b4 0%,#a9c9b9 55%,#6fa35f 80%,#4e8c4a 100%)}
.play{left:344px;top:876px}
.watch{left:172px;top:954px;width:427px;text-align:center;font-size:12px;font-weight:700;color:var(--white)}
.welcome-copy{left:632px;top:798px;width:375px;font-size:14px;line-height:1.55;color:var(--grey)}
.welcome-copy p+p{margin-top:20px}

/* how it works */
.how-band{left:0;top:1097px;width:1200px;height:365px;background:var(--cyan)}
.how-title{left:172px;top:1145px;font-family:"Raleway",sans-serif;font-weight:700;font-size:26px;color:var(--white)}
.how-rule{left:172px;top:1182px;width:44px;height:2px;background:var(--white)}
.steps{left:172px;top:1234px;width:856px;display:flex;gap:20px}
.step{width:199px;color:var(--white);font-size:12.5px;line-height:1.65}
.step svg{display:block;margin-bottom:34px}

/* eligibility */
.elig-title{left:0;top:1515px;width:1200px;font-size:27px}
.elig-sub{left:0;top:1555px;width:1200px;text-align:center;font-size:13px;color:var(--grey)}
.criteria{left:172px;top:1606px;width:856px;display:flex;gap:22px}
.criterion{width:197px;height:127px;border:2px solid #dce6ec;border-radius:60px 8px 60px 8px;display:flex;align-items:center;justify-content:center;text-align:center;font-size:12.5px;font-weight:700;color:var(--ink);letter-spacing:.3px;line-height:1.5}

/* who */
.who-photo{left:0;top:1795px;width:1200px;height:471px;background:linear-gradient(180deg,#2a8fe0 0%,#6cbdf5 45%,#2a4f9a 62%,#d86b2e 82%,#c4592a 100%)}
.who-title{left:176px;top:1845px;font-family:"Raleway",sans-serif;font-weight:700;font-size:33px;color:var(--white)}
.who-copy{left:174px;top:1889px;width:520px;font-size:14.5px;line-height:1.55;color:var(--white)}

/* what next */
.next-line{left:172px;top:2359px;width:856px;height:2px;background:var(--line)}
.next-tab{left:492px;top:2328px;width:234px;height:52px;background:var(--white);border:2px solid var(--line);border-bottom:none;border-radius:10px 10px 0 0;display:flex;align-items:center;justify-content:center;font-family:"Raleway",sans-serif;font-weight:700;font-size:27px;color:var(--navy)}
.next-intro{left:0;top:2397px;width:1200px;text-align:center;font-size:13px;color:var(--grey)}
.next-call{left:0;top:2425px;width:1200px;text-align:center;font-size:25px;font-weight:600;color:var(--navy)}
.next-mail{left:0;top:2460px;width:1200px;text-align:center;font-size:25px;font-weight:600;color:var(--navy)}
.next-call span,.next-mail span{color:var(--cyan-text)}
.next-line-bottom{left:172px;top:2519px;width:856px;height:2px;background:var(--line)}

/* partners */
.partners{left:0;top:2584px;width:1200px;height:226px;background:var(--pale)}
.partners-title{left:0;top:2623px;width:1200px;font-size:17px}
.partners-rule{left:580px;top:2652px;width:40px}
.partner-row{left:172px;top:2690px;width:856px;display:flex;justify-content:space-between;align-items:center}
.badge{background:#c3c9ce}

/* footer */
.site-footer{left:0;top:2810px;width:1200px;height:267px;background:var(--navy)}
.foot-col{top:2838px;color:var(--white);font-size:10.5px;line-height:2.15}
.foot-col h4{font-size:11.5px;font-weight:700;margin-bottom:10px;line-height:1}
.contact-item{display:flex;gap:10px;margin-bottom:10px;line-height:1.55}
.contact-item svg{flex:none;margin-top:2px}
.socials{display:flex;gap:14px;margin-top:4px}
.field{width:196px;height:32px;background:#eef2f6;color:#6b7480;font-size:10.5px;padding-left:10px;display:flex;align-items:center;margin-bottom:10px}
.join{width:196px;height:32px;background:var(--cyan);color:var(--white);font-weight:700;font-size:12px;display:flex;align-items:center;justify-content:center}
.copyright{left:172px;top:3048px;font-size:10px;color:var(--white)}
</style>
</head>
<body>

<header class="abs site-header">
  <div class="abs brand">BRIGHTFIELD HOMES</div>
</header>
<div class="abs call">
  <svg width="24" height="24" viewBox="0 0 24 24" fill="none" stroke="#0b2c5e" stroke-width="1.6"><path d="M5 3h4l2 5-2.5 1.5a11 11 0 0 0 6 6L16 13l5 2v4a2 2 0 0 1-2 2A16 16 0 0 1 3 5a2 2 0 0 1 2-2z"/></svg>
  <div class="call-text"><small>CALL NOW</small><strong>0400 555 271</strong></div>
</div>
<div class="abs quote-btn">REQUEST A QUOTE</div>

<svg class="abs hero-band" width="1200" height="580" viewBox="0 0 1200 580" aria-hidden="true">
  <path d="M0 0H1200V537Q600 620 0 537Z" fill="#0b2c5e"/>
</svg>
<nav class="abs main-nav"><span>HOME</span><span>ABOUT US</span><span>SERVICES</span><span>HOW IT WORKS</span><span>CONTACT US</span></nav>
<div class="abs hero-photo" role="img" aria-label="Photo of a smiling senior man in a sun hat leaning beside rooftop solar panels"></div>
<div class="abs hero-shade"></div>
<div class="abs hero-kicker">HELP PENSIONER HOUSEHOLDS TO</div>
<div class="abs hero-title">SAVE MONEY</div>
<div class="abs hero-copy">And take control of their energy bills by installing an affordable, quality solar system and be part of an Australian first</div>

<h1 class="abs section-title welcome-title">Welcome to Brightfield Homes</h1>
<div class="abs rule welcome-rule"></div>
<div class="abs video-thumb" role="img" aria-label="Illustration of a house with solar panels and wind turbines in a green landscape"></div>
<svg class="abs play" width="82" height="82" viewBox="0 0 82 82" aria-hidden="true"><circle cx="41" cy="41" r="38" fill="none" stroke="#fff" stroke-width="4"/><path d="M32 25L58 41 32 57Z" fill="#fff"/></svg>
<div class="abs watch">WATCH VIDEO</div>
<div class="abs welcome-copy">
  <p>We need you Help pensioner households to save money and take control of their energy bills by installing anaffordable, quality solar system and be part of an Australian first.</p>
  <p>Brightfield Homes is a pioneering approach by Victorian councils to support pensioner households to install solar with no upfront costs. We've done the hard work of finding a safe, reliable and quality installer so pensioners don't have to.</p>
</div>

<section class="abs how-band"></section>
<h2 class="abs how-title">How It Works</h2>
<div class="abs how-rule"></div>
<div class="abs steps">
  <div class="step">
    <svg width="60" height="56" viewBox="0 0 60 56" fill="none" stroke="#fff" stroke-width="2"><circle cx="22" cy="24" r="10"/><path d="M22 4v6M22 38v6M2 24h6M36 24h6M8 10l4 4M32 34l4 4M8 38l4-4M32 14l4-4"/><path d="M44 30v8a6 6 0 0 0 12 0v-8zM48 30v-5M52 30v-5M50 44v8"/></svg>
    Brightfield Homes checks that every person gets a solar system that pays for itself in energy savings from day one
  </div>
  <div class="step">
    <svg width="60" height="56" viewBox="0 0 60 56" fill="none" stroke="#fff" stroke-width="2"><rect x="4" y="4" width="30" height="24"/><path d="M14 4v24M24 4v24M4 12h30M4 20h30M19 28v10"/><rect x="30" y="34" width="24" height="16"/><path d="M36 34v-4h12v4"/></svg>
    Brightfield Homes organises for the solar system to be installed
  </div>
  <div class="step">
    <svg width="60" height="56" viewBox="0 0 60 56" fill="none" stroke="#fff" stroke-width="2"><circle cx="28" cy="18" r="12"/><path d="M10 54c0-12 8-20 18-20s18 8 18 20"/><path d="M42 4l4 4M48 12h5"/></svg>
    Brightfield Homes supports pensioners to understand and get the most out of solar
  </div>
  <div class="step">
    <svg width="60" height="56" viewBox="0 0 60 56" fill="none" stroke="#fff" stroke-width="2"><path d="M10 30h40l6 16H4z"/><path d="M20 30l-3 16M30 30v16M40 30l3 16M6 38h48"/><circle cx="30" cy="12" r="8"/><path d="M30 8v8M27 10h5"/></svg>
    Pensioners gradually pay for cost through their usual rates payments at 0% interest
  </div>
</div>

<h2 class="abs section-title elig-title">Is My Client Eligible?</h2>
<div class="abs elig-sub">Refer clients who are:</div>
<div class="abs criteria">
  <div class="criterion">HOMEOWNERS</div>
  <div class="criterion">PENSION CARD<br>HOLDERS</div>
  <div class="criterion">USUALLY AT HOME<br>FROM 9AM TO 5PM</div>
  <div class="criterion">AVERAGE TO HIGH<br>ELECTRICITY USERS</div>
</div>

<div class="abs who-photo" role="img" aria-label="Photo of solar panels on an orange tiled roof under a bright blue sky with the sun shining"></div>
<h2 class="abs who-title">Who is Brightfield Homes?</h2>
<p class="abs who-copy">Over 20 Victorian councils have come together with support from the Victorian Government's Clean Energy Growth Fund to run the Brightfield Home program.</p>

<div class="abs next-line"></div>
<div class="abs next-tab">What Next?</div>
<p class="abs next-intro">To refer clients or for further information, contact Doug Hollis at Brightfield Homes:</p>
<p class="abs next-call"><span>CALL US :</span> 0400 555 271</p>
<p class="abs next-mail"><span>EMAIL US :</span> doug.hollis@brightfieldhomes.org.au</p>
<div class="abs next-line-bottom"></div>

<section class="abs partners"></section>
<h3 class="abs section-title partners-title">Brightfield Homes is a Partnership Between</h3>
<div class="abs rule partners-rule"></div>
<div class="abs partner-row">
  <div class="badge" style="width:150px;height:70px;border-radius:50%"></div>
  <div class="badge" style="width:192px;height:56px"></div>
  <div class="badge" style="width:170px;height:58px"></div>
  <div class="badge" style="width:110px;height:56px;border-radius:50%"></div>
</div>

<footer class="abs site-footer"></footer>
<div class="abs foot-col" style="left:172px">
  <h4>QUICK LINKS</h4>Home<br>About Us<br>Services<br>How it Works<br>Contact Us
</div>
<div class="abs foot-col" style="left:296px">
  <h4>SUPPORT</h4>Contact us<br>FAQs<br>Legal<br>Privacy Policy<br>Legal
</div>
<div class="abs foot-col" style="left:414px">
  <h4>CONTACT US</h4>
  <div class="contact-item"><svg width="22" height="22" viewBox="0 0 22 22" fill="none" stroke="#fff" stroke-width="1.5"><circle cx="11" cy="11" r="10"/><path d="M11 5a4 4 0 0 1 4 4c0 3-4 8-4 8s-4-5-4-8a4 4 0 0 1 4-4z"/></svg><span>Your Company LTD.<br>Street Name, 000000<br>City Name</span></div>
  <div class="contact-item"><svg width="22" height="22" viewBox="0 0 22 22" fill="none" stroke="#fff" stroke-width="1.5"><circle cx="11" cy="11" r="10"/><path d="M8 6h2l1 3-1.5 1a6 6 0 0 0 3 3L14 11.5l3 1V15a1 1 0 0 1-1 1A9 9 0 0 1 7 7a1 1 0 0 1 1-1z"/></svg><span>Phone<br>0400 555 271</span></div>
  <div class="contact-item"><svg width="22" height="22" viewBox="0 0 22 22" fill="none" stroke="#fff" stroke-width="1.5"><circle cx="11" cy="11" r="10"/><rect x="6" y="8" width="10" height="7"/><path d="M6 8l5 4 5-4"/></svg><span>Email<br>doug.hollis@brightfieldhomes.org.au</span></div>
</div>
<div class="abs foot-col" style="left:648px">
  <h4>GET CONNECTED</h4>
  <div class="socials" aria-label="Social links">
    <svg width="20" height="20" viewBox="0 0 20 20"><circle cx="10" cy="10" r="8.5" fill="none" stroke="#fff" stroke-width="1.5"/></svg>
    <svg width="20" height="20" viewBox="0 0 20 20"><circle cx="10" cy="10" r="8.5" fill="none" stroke="#fff" stroke-width="1.5"/></svg>
    <svg width="20" height="20" viewBox="0 0 20 20"><circle cx="10" cy="10" r="8.5" fill="none" stroke="#fff" stroke-width="1.5"/></svg>
    <svg width="20" height="20" viewBox="0 0 20 20"><circle cx="10" cy="10" r="8.5" fill="none" stroke="#fff" stroke-width="1.5"/></svg>
  </div>
</div>
<div class="abs foot-col" style="left:830px">
  <h4>E-NEWSLETTER SIGNUP</h4>
  <div class="field">Name</div>
  <div class="field">Email</div>
  <div class="join">JOIN</div>
</div>
<div class="abs copyright">© 2017 Brightfield Homes. All Rights Reserved</div>

</body>
</html>
```